Webpage - LORAVEN.COM (Webpage)

Design webpage for LoRaven.com (already own the domain).
At a minimum the webpage should include links and information about:
1. BRAND - https://amberwoodliving.example/
2. SONGS – link to artist and all released songs (3 currently available under Lora Venn on Streamly and other platforms). Ability to add songs as they are released.
3. PODCAST - Links to existing (2) and upcoming podcasts "Days Run Golden" (currently available on Streamly, Viewtube and other platforms). Ability to add links to future podcasts.
https://video.example/watch?v=Q-3KtHbWr8Za
4. VOICE COACH - Information about voice coaching/lessons by Lora Venn as well as how to contact regarding the lessons. Ability to add testimonials. Add "click here" link for requesting more information regarding voice lessons, with fields like name, email, cell phone and best method, time to contact that user can fill to request info
5. SOCIAL MEDIA -Links to Lora Venn's Lensfeed, Gatherly, TikTok, Viewtube Channel (not yet created), etc.
6. BAND - Link to access information about band “Lora Venn and KOBALTT
https://social.example/kobalttband/?next=%2Fmirelotsan%2Ffeed%2F&locale=en_US%2Cen_US. Add "click here" link for requesting more information regarding voice lessons, with fields like name, email, cell phone and best method, time to contact that user can fill to request info
7. VIDEOS – links to music and promotional videos from solo artist and band. All will eventually be compiled on Viewtube channel.
Pictures are included for reference and use but not necessarily asking that they all be on the website. Designer can use discretion from uploaded files or request more if desired.

Coding

Coded - Design and coding required

Number of Pages Required

1 page

Requirements
Must have
• Original artist song plays when opening page. Preferably Hold the Quiet Near or HQN.
Nice to have
• Rotating songs play when clicking any link

```html
<!DOCTYPE html>
<html lang="en">
<head>
<meta charset="utf-8">
<title>Lora Venn</title>
<link rel="stylesheet" href="https://fonts.googleapis.com/css2?family=PT+Serif:wght@400;700&display=swap">
<style>
:root{
  --accent:#dc3447;
  --orange:#e8401c;
  --yellow:#e2d86c;
  --cream:#f8f5e3;
  --ink:#1f1f1f;
  --muted:#555;
  --green:#2fb35b;
  --footer:#3a3a3a;
  --line:#cfcfcf;
}
*{box-sizing:border-box;margin:0;padding:0}
html,body{width:1200px;height:3941px;overflow:hidden}
body{position:relative;background:#fff;font-family:"PT Serif",serif;color:var(--ink)}
.abs{position:absolute}
.btn{position:absolute;display:flex;align-items:center;justify-content:center;background:var(--accent);color:#fff;border-radius:30px;font-size:13px;text-transform:uppercase;text-decoration:none}
.media{position:absolute}
.heading{position:absolute;left:0;width:1200px;text-align:center;font-weight:400;font-size:52px;letter-spacing:1px}

/* header */
.topline{top:0;left:0;width:1200px;height:4px;background:var(--orange)}
.brand{left:145px;top:22px;display:flex;align-items:center;gap:10px;font-size:30px;font-weight:700}
.brand .dot{width:46px;height:46px;border-radius:50%;background:var(--yellow)}
.search{left:745px;top:14px;width:175px;height:22px;border-bottom:1px solid var(--line);font-size:11px;padding-left:2px;line-height:20px;color:var(--muted)}
.nav{left:453px;top:54px;display:flex;gap:28px;font-size:12px}
.nav a{color:var(--ink);text-decoration:none;padding-bottom:4px}
.nav a.active{border-bottom:2px solid var(--accent)}
.lang{left:990px;top:20px;font-size:11px;color:var(--muted)}

/* hero */
.hero-left{left:0;top:88px;width:652px;height:534px;background:linear-gradient(120deg,#bfb34a 0%,#d8cd62 22%,#e4da76 45%,#cfc35a 70%,#b8ac48 100%)}
.hero-right{left:658px;top:88px;width:542px;height:534px;background:linear-gradient(170deg,#e9c9d4 0%,#d9a9b6 25%,#b8707c 45%,#8a3a42 62%,#a8343a 78%,#4a1e22 100%)}
.hero-title{left:145px;top:200px;font-size:72px;letter-spacing:1px;font-weight:400}
.hero-text{left:145px;top:308px;width:400px;font-size:20px;line-height:28px}
.hero-dots{left:145px;top:521px;display:flex;gap:14px}
.hero-dots span{width:12px;height:12px;border-radius:50%;background:#fff}
.hero-dots span.on{background:var(--accent)}
.swap{left:630px;top:333px;width:44px;height:44px;border-radius:50%;background:#fff;display:flex;align-items:center;justify-content:center;font-size:14px}

/* songs */
.song{position:absolute;left:177px;width:415px;height:98px;border:1px solid #bbb;background:#fff}
.song.on{border:2px solid var(--green)}
.song .thumb{position:absolute;left:15px;top:10px;width:83px;height:78px}
.song .title{position:absolute;left:135px;top:14px;width:200px;font-size:14px;line-height:20px}
.song .artist{position:absolute;left:135px;top:66px;font-size:11px;color:var(--accent);display:flex;align-items:center;gap:5px}
.song .artist i{width:10px;height:10px;border-radius:50%;background:var(--yellow)}
.song .platform{position:absolute;right:52px;top:68px;font-size:11px;display:flex;align-items:center;gap:4px}
.song .platform i{width:14px;height:14px;border-radius:50%;background:var(--green)}
.song .platform.vt i{border-radius:2px;background:var(--accent)}
.song .heart{position:absolute;right:14px;top:12px}
.song .more{position:absolute;right:22px;top:62px;width:3px;height:18px;background:radial-gradient(circle,#999 1.2px,transparent 1.5px) 0 0/3px 6px}
.song-video{left:608px;top:778px;width:414px;height:332px;background:linear-gradient(160deg,#d84a48 0%,#b8302e 30%,#7a2a2a 55%,#2e2a2e 75%,#8a7a6a 100%)}
.play{position:absolute;width:34px;height:34px;border-radius:50%;background:var(--accent);display:flex;align-items:center;justify-content:center}

/* podcasts */
.podcasts{left:0;top:1275px;width:1200px;height:615px;background:var(--cream)}
.pod{position:absolute;top:1440px;width:295px;height:325px;background:#fff;border:2px solid #ddd}
.pod.on{height:365px;background:var(--yellow);border-color:#d8ce64}
.pod .img{position:absolute;left:8px;top:8px;width:275px;height:172px}
.pod .badge{position:absolute;right:16px;top:164px;width:30px;height:30px;border-radius:50%;background:var(--accent);border:3px solid #fff}
.pod h3{position:absolute;left:28px;top:196px;width:230px;font-size:16px;line-height:22px;font-weight:700}
.pod p{position:absolute;left:28px;top:250px;width:220px;font-size:12px;line-height:17px;color:#444}
.pod .btn{left:28px;top:307px;width:110px;height:34px}
.arrow{position:absolute;top:1601px;width:44px;height:44px;border-radius:50%;border:1px solid #999;display:flex;align-items:center;justify-content:center}

/* gallery strip */
.strip{top:1890px;height:292px}

/* voice coach */
.vc-frame{left:530px;top:2255px;width:525px;height:445px;border:2px solid #ddd}
.vc-outline{left:95px;top:2440px;width:300px;height:243px;border:2px solid var(--orange);border-right:none}
.vc-photo1{left:147px;top:2250px;width:383px;height:395px;background:linear-gradient(165deg,#5a2a30 0%,#c04a78 22%,#e088a4 40%,#9a4a5a 62%,#e8d8a0 80%,#2a1a24 100%)}
.vc-photo2{left:357px;top:2500px;width:198px;height:205px;background:linear-gradient(135deg,#e03a2a 0%,#b01818 40%,#6a0c0c 75%,#2a0606 100%);border:4px solid #fff}
.vc-title{left:600px;top:2318px;font-size:54px;font-weight:400}
.vc-text{left:600px;top:2400px;width:418px;font-size:12.5px;line-height:26px;text-align:justify;color:#333}

/* band */
.band{top:2780px;height:102px;display:flex;align-items:center;justify-content:center;font-size:38px;font-weight:700}
.band.solo{left:0;width:595px;background:var(--orange);color:#fff}
.band.group{left:595px;width:605px;background:var(--yellow);color:var(--ink)}

/* follow */
.tile{position:absolute}

/* footer */
.footer{left:0;top:3683px;width:1200px;height:258px;background:var(--footer);color:#fff}
.cards{left:410px;top:3722px;display:flex;gap:4px}
.cards span{width:34px;height:18px;background:#fff;border-radius:3px;color:var(--footer);font-size:8px;line-height:18px;text-align:center}
.fnav{left:0;top:3778px;width:1200px;display:flex;justify-content:center;gap:47px;font-size:15px}
.fnav a{color:#fff;text-decoration:none}
.copy{left:0;top:3834px;width:1200px;text-align:center;font-size:12px}
.social{top:3878px;display:flex;align-items:center;gap:5px;font-size:11px}
.social i{width:32px;height:32px;border-radius:50%;border:2px solid #fff}
.social.on i{background:var(--accent)}
</style>
</head>
<body>

<!-- header -->
<div class="abs topline"></div>
<div class="abs brand"><span class="dot"></span>Lora Venn</div>
<div class="abs search">Search</div>
<svg class="abs" style="left:906px;top:16px" width="12" height="12" viewBox="0 0 12 12"><circle cx="5" cy="5" r="3.6" fill="none" stroke="#222" stroke-width="1.6"/><line x1="7.6" y1="7.6" x2="11" y2="11" stroke="#222" stroke-width="1.8"/></svg>
<svg class="abs" style="left:944px;top:14px" width="26" height="22" viewBox="0 0 26 22"><path d="M1 3h4l3 12h13l3-9H7" fill="none" stroke="#222" stroke-width="1.8"/><circle cx="10" cy="19" r="1.8" fill="#222"/><circle cx="19" cy="19" r="1.8" fill="#222"/></svg>
<div class="abs lang">▭ ENG ▾</div>
<nav class="abs nav">
  <a class="active" href="#">HOME</a><a href="#">BRAND</a><a href="#">SONGS</a><a href="#">PODCAST</a><a href="#">VOICE COACH</a><a href="#">BAND</a><a href="#">VIDEOS</a><a href="#">CONTACT</a>
</nav>

<!-- hero -->
<div class="media hero-left" role="img" aria-label="Band performing on stage, washed in yellow"></div>
<div class="media hero-right" role="img" aria-label="Portrait of Lora Venn in a cap and plaid shirt"></div>
<h1 class="abs hero-title">LORA VENN</h1>
<p class="abs hero-text">Sed ut perspiciatis unde omnis iste natus error sit voluptdoloremque atem</p>
<a class="btn" href="#" style="left:145px;top:405px;width:157px;height:55px;font-weight:700">Shop Now</a>
<div class="abs hero-dots"><span></span><span class="on"></span><span></span></div>
<div class="abs swap">← →</div>

<!-- songs -->
<h2 class="heading" style="top:680px">SONGS</h2>
<div class="song on" style="top:778px">
  <div class="thumb" style="background:linear-gradient(150deg,#6a2a2a,#c84a3a 45%,#e8c8b0 70%,#3a3a4a)" role="img" aria-label="Song cover: band on stage"></div>
  <div class="title">Voluptatem accusantium dolormqudantium</div>
  <div class="artist"><i></i>Lora Venn</div>
  <div class="platform"><i></i>Streamly</div>
  <svg class="heart" width="14" height="12" viewBox="0 0 14 12"><path d="M7 12L1 6A3.3 3.3 0 0 1 7 2a3.3 3.3 0 0 1 6 4z" fill="var(--green)"/></svg>
  <span class="more"></span>
</div>
<div class="song" style="top:894px">
  <div class="thumb" style="background:linear-gradient(160deg,#1a2a3a,#5a8a9a 40%,#2a3a2a 65%,#a83a3a)" role="img" aria-label="Song cover: concert with lights"></div>
  <div class="title">Voluptatem accusantium dolormqudantium</div>
  <div class="artist"><i></i>Lora Venn</div>
  <div class="platform vt"><i></i>Viewtube</div>
  <svg class="heart" width="14" height="12" viewBox="0 0 14 12"><path d="M7 12L1 6A3.3 3.3 0 0 1 7 2a3.3 3.3 0 0 1 6 4z" fill="var(--green)"/></svg>
  <span class="more"></span>
</div>
<div class="song" style="top:1010px">
  <div class="thumb" style="background:linear-gradient(140deg,#2a2a30,#8a8a90 40%,#3a3a40 70%,#c0b0a0)" role="img" aria-label="Song cover: band portrait"></div>
  <div class="title">Voluptatem accusantium dolormqudantium</div>
  <div class="artist"><i></i>Lora Venn</div>
  <div class="platform"><i></i>Streamly</div>
  <svg class="heart" width="14" height="12" viewBox="0 0 14 12"><path d="M7 12L1 6A3.3 3.3 0 0 1 7 2a3.3 3.3 0 0 1 6 4z" fill="var(--green)"/></svg>
  <span class="more"></span>
</div>
<div class="media song-video" role="img" aria-label="Music video still: Lora Venn seated in a stadium"></div>
<div class="play" style="left:798px;top:928px"><svg width="12" height="14" viewBox="0 0 12 14"><path d="M1 1l10 6-10 6z" fill="#fff"/></svg></div>
<a class="btn" href="#" style="left:522px;top:1158px;width:156px;height:54px;font-weight:700">View More</a>

<!-- podcasts -->
<div class="abs podcasts"></div>
<h2 class="heading" style="top:1345px">PODCASTS</h2>
<div class="arrow" style="left:76px"><svg width="10" height="16" viewBox="0 0 10 16"><path d="M8 1L2 8l6 7" fill="none" stroke="#333" stroke-width="2"/></svg></div>
<div class="arrow" style="left:1079px"><svg width="10" height="16" viewBox="0 0 10 16"><path d="M2 1l6 7-6 7" fill="none" stroke="#333" stroke-width="2"/></svg></div>
<div class="pod" style="left:145px">
  <div class="img" style="background:linear-gradient(170deg,#e8e8e8,#b0b0b0 35%,#f0f0f0 55%,#3a3a3a 85%,#1a1a1a)" role="img" aria-label="Black and white band group photo"></div><span class="badge"></span>
  <h3>Voluptatem accusantium dolormqudantium</h3>
  <p>Woluptatem accusantium dolor emque laudantium</p>
  <a class="btn" href="#">Read More</a>
</div>
<div class="pod on" style="left:453px">
  <div class="img" style="background:linear-gradient(170deg,#2a2420,#8a7a60 35%,#e8e4dc 60%,#c8c0b0 80%,#3a3028)" role="img" aria-label="Band seated with instruments"></div><span class="badge"></span>
  <h3>Voluptatem accusantium dolormqudantium</h3>
  <p>Woluptatem accusantium dolor emque laudantium</p>
  <a class="btn" href="#">Read More</a>
</div>
<div class="pod" style="left:760px">
  <div class="img" style="background:linear-gradient(90deg,#2a2a2e,#8a8a90 30%,#dcdcdc 50%,#7a7a80 70%,#2a2a2e)" role="img" aria-label="Singer posing in a stadium tunnel"></div><span class="badge"></span>
  <h3>Voluptatem accusantium dolormqudantium</h3>
  <p>Woluptatem accusantium dolor emque laudantium</p>
  <a class="btn" href="#">Read More</a>
</div>

<!-- video strip -->
<div class="media strip" style="left:0;width:388px;background:linear-gradient(160deg,#1a2420 0%,#4a5a50 25%,#b8c8d0 45%,#2a3a30 65%,#a02a2a 85%,#1a1a1a 100%)" role="img" aria-label="Performance at a holiday stage"></div>
<div class="media strip" style="left:396px;width:407px;background:linear-gradient(135deg,#5a0a06 0%,#c8401e 30%,#8a1a10 55%,#d05a3a 75%,#2a0604 100%)" role="img" aria-label="Band on stage in red light"></div>
<div class="media strip" style="left:812px;width:388px;background:linear-gradient(160deg,#0e0a2a 0%,#3a2a8a 25%,#c030b0 50%,#6a1a7a 72%,#e050d0 88%,#1a0a2a 100%)" role="img" aria-label="Crowd at a concert with purple lights"></div>
<div class="play" style="left:583px;top:2020px"><svg width="12" height="14" viewBox="0 0 12 14"><path d="M1 1l10 6-10 6z" fill="#fff"/></svg></div>

<!-- voice coach -->
<div class="abs vc-frame"></div>
<div class="abs vc-outline"></div>
<div class="media vc-photo1" role="img" aria-label="Lora Venn singing in a pink cap"></div>
<div class="media vc-photo2" role="img" aria-label="Lora Venn performing in red light"></div>
<h2 class="abs vc-title">VOICE COACH</h2>
<p class="abs vc-text">Sed ut perspiciatis unde omnis iste natus error sit voluptatem accusantium doloremque laudantium, totam rem aperiam, eaque ipsa quae ab illo inventore veritatis et quasi architecto beatae vitae dicta sunt explicabo. Nemo enim ipsam voluptatem quia voluptas sit aspernatur aut odit aut fugit, sed quia consequuntur magni dolores eos qui ratione voluptatem sequi nesciunt. Neque porro quisquam est, qui dolorem ipsum quia dolor sit amet,</p>
<a class="btn" href="#" style="left:600px;top:2603px;width:111px;height:37px">Read More</a>

<!-- band -->
<div class="abs band solo">LORA VENN</div>
<div class="abs band group">KOBALTT</div>

<!-- follow -->
<h2 class="heading" style="top:2960px">FOLLOW US</h2>
<div class="tile" style="left:145px;top:3053px;width:300px;height:250px;background:linear-gradient(150deg,#2a2218 0%,#6a5a40 25%,#e8e0d0 50%,#3a3020 70%,#d8d0c0 100%)" role="img" aria-label="Band lounging with keyboard"></div>
<div class="tile" style="left:450px;top:3053px;width:300px;height:250px;background:linear-gradient(160deg,#0a1020 0%,#2a3a4a 35%,#5a6a7a 55%,#1a2230 80%,#0a0e18 100%)" role="img" aria-label="Singer dancing on a balcony at night"></div>
<div class="tile" style="left:756px;top:3053px;width:299px;height:250px;background:linear-gradient(150deg,#8a5a3a 0%,#c89a7a 30%,#7aa0c8 50%,#3a2a28 75%,#d8c0b0 100%)" role="img" aria-label="Friends dancing indoors"></div>
<div class="tile" style="left:145px;top:3309px;width:300px;height:251px;background:linear-gradient(150deg,#5a2a2a 0%,#e0a0a8 35%,#8a5a5a 60%,#c8a080 80%,#3a2a2a 100%)" role="img" aria-label="Performer in pink at a show"></div>
<div class="tile" style="left:450px;top:3309px;width:300px;height:251px;background:linear-gradient(150deg,#2a241c 0%,#8a7a60 30%,#e8e0d0 55%,#5a4a38 75%,#c0b090 100%)" role="img" aria-label="Band posing with guitars"></div>
<div class="tile" style="left:756px;top:3309px;width:299px;height:251px;background:linear-gradient(150deg,#2a1a3a 0%,#8a4a5a 30%,#e8d0c0 55%,#f0f0f0 75%,#c83030 100%)" role="img" aria-label="Two friends holding a shirt"></div>
<svg class="abs" style="left:584px;top:3166px" width="32" height="32" viewBox="0 0 32 32"><circle cx="16" cy="16" r="14" fill="none" stroke="#fff" stroke-width="2.5"/></svg>
<a class="btn" href="#" style="left:545px;top:3594px;width:110px;height:36px">Load More</a>

<!-- footer -->
<footer class="abs footer"></footer>
<div class="abs cards"><span>Arlo</span><span>Pear</span><span>Dune</span><span>Vela</span><span>Mova</span><span>Gira</span><span>Tern</span><span>Palo</span><span>Shoa</span><span>Nova</span></div>
<nav class="abs fnav"><a href="#">HOME</a><a href="#">BRAND</a><a href="#">SONGS</a><a href="#">PODCAST</a><a href="#">VOICE COACH</a><a href="#">BAND</a><a href="#">VIDEOS</a><a href="#">CONTACT</a></nav>
<p class="abs copy" style="color:#fff">© 2024 Companyname.All Rights Reserved &nbsp;|&nbsp; Privacy &nbsp;|&nbsp; Terms of Use</p>
<div class="abs social" style="left:470px;color:#fff"><span>Gatherly</span><i></i></div>
<div class="abs social on" style="left:584px;color:#fff"><i></i></div>
<div class="abs social" style="left:634px;color:#fff"><i></i><span>Viewtube</span></div>

</body>
</html>
```